Brindle Sky Port needs a new upscale business card design for our high end aircraft hangar complex

Brindle Sky Port (BSP) is a large, upscale jet hangar complex in the US housing expensive aircraft. We need a new business card design, using our current logo. We will be attending a industry convention and need a card design that will stand out and be remembered by aircraft owners and private pilots.

Target Market(s)

Aircraft pilots or owners looking for a new upscale hangar

Industry/Entity Type

Airport

Contact Information for Business Card

I like to use very heavy card stock, 400#, double sided. Square, no rounded edges please.

Colors
3276b5
0255a3
85abd2

Requirements
Must have
• An expensive, classy design, vivid colors.
Nice to have
• Needs to look very expensive and classy, and have some "pop". Designer must be able to download or copy my current typeface or fonts.
• One card side might be black with the "Logo and Brindle Sky Port Double line image in blue (or try gold, or glossy black), and perhaps have a grayed out "K720 jet silhouette". The other card side would have our contact info, and perhaps the "BSP Logo only". I'd like my contact info 'stacked', not in a paragraph format.
Should not have
• Should not look "too busy". Having a double-sided card will help.

```html
<!DOCTYPE html>
<html lang="en">
<head>
<meta charset="utf-8">
<title>Brindle Sky Port — Business Card</title>
<link href="https://fonts.googleapis.com/css2?family=Open+Sans:wght@400;600;700&display=swap" rel="stylesheet">
<style>
  :root {
    --backdrop: #ececec;
    --silver-light: #eeeeee;
    --silver-mid: #d4d4d4;
    --silver-dark: #bdbdbd;
    --band-top: #4a4f57;
    --band-bottom: #050505;
    --brand-blue: #3276b5;
    --brand-deep: #0255a3;
    --brand-sky: #85abd2;
    --text-light: #ffffff;
    --text-muted: #d2d2d2;
    --divider: #5a6f86;
  }
  html, body {
    margin: 0;
    padding: 0;
    width: 1200px;
    height: 900px;
    overflow: hidden;
    background: var(--backdrop);
    font-family: "Open Sans", Arial, sans-serif;
  }
  .canvas {
    position: relative;
    width: 1200px;
    height: 900px;
  }
  .card {
    position: absolute;
    overflow: hidden;
    box-shadow: 0 6px 18px rgba(0,0,0,0.25);
  }
  .silver {
    background: linear-gradient(100deg, var(--silver-dark) 0%, var(--silver-light) 45%, var(--silver-mid) 100%);
  }
  .band {
    background: linear-gradient(180deg, var(--band-top) 0%, #22262c 45%, var(--band-bottom) 100%);
  }
  .accent-rule {
    position: absolute;
    left: 0;
    width: 100%;
    height: 4px;
    background: linear-gradient(90deg, var(--brand-deep) 0%, var(--brand-blue) 50%, var(--brand-sky) 100%);
  }

  /* Front card: contact side */
  .card-front { left: 78px; top: 33px; width: 587px; height: 364px; }
  .card-front .logo-area { position: absolute; left: 0; top: 0; width: 100%; height: 192px; }
  .card-front .contact-band { position: absolute; left: 0; top: 192px; width: 100%; height: 172px; }
  .card-front .accent-rule { top: 190px; }

  .wordmark {
    position: absolute;
    left: 0; width: 100%;
    text-align: center;
    font-weight: 700;
    line-height: 1;
  }
  .card-front .wordmark { color: var(--brand-deep); }
  .card-front .wordmark-initials { top: 54px; font-size: 76px; letter-spacing: 4px; }
  .card-front .wordmark-name { top: 140px; font-size: 27px; }

  .person {
    position: absolute;
    right: 297px; top: 224px;
    text-align: right;
    color: var(--text-light);
  }
  .person-name { font-size: 20px; color: var(--text-muted); margin: 0; line-height: 24px; }
  .person-title { font-size: 15px; margin: 0 0 12px; line-height: 22px; }
  .person-address { font-size: 15px; margin: 0; line-height: 19px; }

  .contact-divider {
    position: absolute;
    left: 309px; top: 222px;
    width: 1px; height: 96px;
    background: var(--divider);
  }
  .contact-list {
    position: absolute;
    left: 330px; top: 222px;
    margin: 0; padding: 0;
    list-style: none;
    color: var(--text-light);
    font-size: 15px;
  }
  .contact-list li {
    display: flex;
    align-items: center;
    height: 24.5px;
  }
  .contact-list svg { width: 12px; height: 12px; margin-right: 10px; fill: var(--brand-sky); }

  /* Back card: logo side */
  .card-back { left: 388px; top: 505px; width: 567px; height: 352px; }
  .card-back .band-upper { position: absolute; left: 0; top: 0; width: 100%; height: 90px; }
  .card-back .logo-band { position: absolute; left: 0; top: 90px; width: 100%; height: 173px; }
  .card-back .band-lower { position: absolute; left: 0; top: 263px; width: 100%; height: 89px; }
  .card-back .rule-top { top: 88px; }
  .card-back .rule-bottom { top: 261px; }
  .card-back .wordmark { color: var(--brand-sky); }
  .card-back .wordmark-initials { top: 120px; font-size: 74px; letter-spacing: 4px; }
  .card-back .wordmark-name { top: 213px; font-size: 26px; }
</style>
</head>
<body>
<main class="canvas">

  <section class="card card-front" aria-label="Business card, contact side">
    <div class="logo-area silver"></div>
    <div class="contact-band band"></div>
    <div class="accent-rule"></div>
    <div class="wordmark wordmark-initials">BSP</div>
    <div class="wordmark wordmark-name">Brindle Sky Port</div>

    <div class="person">
      <p class="person-name">Daniel Harper</p>
      <p class="person-title">Managing Director</p>
      <p class="person-address">12345, Address Goes Here<br>Country Name, 123456</p>
    </div>

    <div class="contact-divider"></div>

    <ul class="contact-list">
      <li>
        <svg viewBox="0 0 24 24" aria-hidden="true"><path d="M6.6 10.8a15.1 15.1 0 0 0 6.6 6.6l2.2-2.2a1 1 0 0 1 1-.25 11.4 11.4 0 0 0 3.6.57 1 1 0 0 1 1 1V20a1 1 0 0 1-1 1A17 17 0 0 1 3 4a1 1 0 0 1 1-1h3.5a1 1 0 0 1 1 1c0 1.25.2 2.45.57 3.57a1 1 0 0 1-.25 1z"/></svg>
        (044)-456-7890
      </li>
      <li>
        <svg viewBox="0 0 24 24" aria-hidden="true"><path d="M9 3h6v3h5a1 1 0 0 1 1 1v12a1 1 0 0 1-1 1H4a1 1 0 0 1-1-1V7a1 1 0 0 1 1-1h5zm2 0v3h2V3z M6 10h12v2H6z"/></svg>
        123-456-7890
      </li>
      <li>
        <svg viewBox="0 0 24 24" aria-hidden="true"><path d="M2 5h20v14H2zm2 2v.5l8 5 8-5V7z"/></svg>
        info@youremail.com
      </li>
      <li>
        <svg viewBox="0 0 24 24" aria-hidden="true"><circle cx="12" cy="12" r="10"/></svg>
        www.website.com
      </li>
    </ul>
  </section>

  <section class="card card-back" aria-label="Business card, logo side">
    <div class="band-upper silver"></div>
    <div class="logo-band band"></div>
    <div class="band-lower silver"></div>
    <div class="accent-rule rule-top"></div>
    <div class="accent-rule rule-bottom"></div>
    <div class="wordmark wordmark-initials">BSP</div>
    <div class="wordmark wordmark-name">Brindle Sky Port</div>
  </section>

</main>
</body>
</html>
```